Business Card Design Project

Business Card
We are rebranding with a new logo
Industry/Entity Type
Business
Contact Information for Business Card
Dennis Morvale +61 487215963 dennis@quorv.com.au P.O. Box 872 Fernlow QLD 4309
Requirements
Must have
- Logo

```html
<!DOCTYPE html>
<html lang="en">
<head>
<meta charset="utf-8">
<title>Quorv International – Business Card</title>
<link rel="stylesheet" href="https://fonts.googleapis.com/css2?family=Roboto:wght@400;700&family=Roboto+Condensed:wght@700&display=swap">
<style>
  :root {
    --backdrop: #2b2b2b;
    --card: #f4f4f4;
    --brand-blue: #1787c2;
    --ink: #474747;
    --band-orange: #ec8a1e;
    --band-text: #ffffff;
  }
  * { margin: 0; padding: 0; box-sizing: border-box; }
  html, body {
    width: 1200px;
    height: 960px;
    overflow: hidden;
    background: var(--backdrop);
  }
  .canvas {
    position: relative;
    width: 1200px;
    height: 960px;
  }
  .business-card {
    position: absolute;
    left: 407px;
    top: 143px;
    width: 386px;
    height: 675px;
    background: var(--card);
    border-radius: 22px;
    overflow: hidden;
    text-align: center;
    font-family: "Roboto", sans-serif;
    color: var(--ink);
  }
  .brand-name {
    position: absolute;
    left: 0;
    right: 0;
    top: 150px;
    font-family: "Roboto Condensed", sans-serif;
    font-weight: 700;
    color: var(--brand-blue);
    line-height: 1.05;
  }
  .brand-name .primary {
    display: block;
    font-size: 64px;
    letter-spacing: 1px;
  }
  .brand-name .secondary {
    display: block;
    font-size: 22px;
    letter-spacing: 5px;
    margin-top: 6px;
  }
  .holder-name {
    position: absolute;
    left: 0;
    right: 0;
    top: 397px;
    font-family: "Roboto Condensed", sans-serif;
    font-weight: 700;
    font-size: 37px;
    color: var(--brand-blue);
  }
  .phone {
    position: absolute;
    left: 0;
    right: 0;
    top: 466px;
    font-weight: 700;
    font-size: 22px;
  }
  .address-block {
    position: absolute;
    left: 0;
    right: 0;
    top: 512px;
    font-size: 16px;
    line-height: 22px;
  }
  .web-band {
    position: absolute;
    left: 0;
    right: 0;
    top: 603px;
    height: 33px;
    background: var(--band-orange);
    color: var(--band-text);
    font-size: 16px;
    letter-spacing: 3px;
    line-height: 33px;
  }
</style>
</head>
<body>
<main class="canvas">
  <article class="business-card">
    <div class="brand-name">
      <span class="primary">QUORV</span>
      <span class="secondary">INTERNATIONAL</span>
    </div>
    <h1 class="holder-name">DENNIS MORVALE</h1>
    <p class="phone">+61 487215963</p>
    <p class="address-block">
      P.O. Box 872 , Fernlow QLD 4309<br>
      dennis@quorv.com.au
    </p>
    <div class="web-band">www.quorv.com.au</div>
  </article>
</main>
</body>
</html>
```